Insert sheet for our Dog Food Package

We need an information sheet to go inn our pet food package, with branding, and information on ingredients, nutrition and feeding guidance. We will also need two additional items which will be a variation on the label design:
1) Label for package (detailed label about us and our food)
2) Label for outer shipping box (simple label for branding)
We will start with the information, insert page. The winning designer will then deliver the package and box labels as simplified versions of the same graphical theme.
I have attached samples of an earlier drafts of the insert piece. Please disregard the style, form and colors of the examples given. THEY ARE ONLY THERE TO SHOW WHAT INFORMATION SHOULD BE INCLUDED. All colors and style should be from our logo (attached). All graphics, font styles, and placement of elements need to be YOUR creative design - not a copy of the sample we gave. PLEASE READ THIS AND PLEASE DO NOT SUBMIT ANY VARIATION OF THE EXAMPLES!!!!!!!

Target Market(s)

Pet Owners

Industry/Entity Type

Pet Food

Colors
EB3D1F
EC4F4E
F09395
F8D3D4
FCEDEE

Requirements
Must have
• All new design. New colors (based in the palette of our logo), new graphics, new fonts, new placement of elements.
Should not have
• Please disregard the style, form and colors of the examples given. THEY ARE ONLY THERE TO SHOW WHAT INFORMATION SHOULD BE INCLUDED.

```html
<!DOCTYPE html>
<html lang="en">
<head>
<meta charset="utf-8">
<title>Verra – Feeding Insert for Shadow</title>
<link rel="stylesheet" href="https://fonts.googleapis.com/css2?family=Poppins:wght@400;500;600;700;800;900&display=swap">
<style>
  :root{
    --red:#a9170f;
    --red-deep:#8e120b;
    --red-bright:#c4231a;
    --brown:#3e1008;
    --ink:#1f1a19;
    --white:#ffffff;
    --grey:#d6d6d6;
    --grey-row:#ebebeb;
    --dot-mid:#7a2c1f;
    --dot-light:#c8a9a3;
    --stage:#eceef1;
  }
  *{margin:0;padding:0;box-sizing:border-box}
  html,body{width:1200px;height:2400px;overflow:hidden}
  body{background:var(--stage);font-family:"Poppins",sans-serif;color:var(--ink);position:relative}

  .insert{position:absolute;left:40px;top:408px;width:1120px;height:1584px;background:var(--white);overflow:hidden;box-shadow:6px 10px 18px rgba(0,0,0,.28)}

  .hero-band{position:absolute;left:0;top:0;width:1120px;height:600px}
  .foot-band{position:absolute;left:0;top:1370px;width:1120px;height:214px}

  .brand-tab{position:absolute;left:62px;top:0;width:375px;height:210px;background:var(--white);border-radius:0 0 30px 30px;display:flex;align-items:center;justify-content:center;gap:18px}
  .brand-dot{width:86px;height:86px;border-radius:50%;background:var(--red)}
  .brand-name{font-weight:700;font-size:54px;letter-spacing:4px;color:var(--red)}

  .dog-photo{position:absolute;left:496px;top:17px;width:624px;height:792px}

  .headline{position:absolute;left:62px;top:282px;font-weight:900;font-size:84px;line-height:76px;color:var(--white);letter-spacing:.5px;text-transform:uppercase}

  .story-title{position:absolute;left:62px;top:636px;font-weight:800;font-size:66px;line-height:72px;color:var(--brown)}
  .story-title span{color:var(--red)}
  .story-dots{position:absolute;left:64px;top:716px;display:flex;gap:5px}
  .story-dots i{width:11px;height:11px;border-radius:50%;background:var(--brown)}
  .story-dots i:nth-child(2){background:var(--dot-mid)}
  .story-dots i:nth-child(3){background:var(--dot-light)}
  .story-lead{position:absolute;left:62px;top:740px;width:560px;font-weight:700;font-size:19px;line-height:25px;letter-spacing:-.3px;color:var(--ink)}

  .quote-box{position:absolute;left:62px;top:871px;width:996px;height:162px;border:2px dashed #8a8a8a;border-radius:18px}
  .quote-mark{position:absolute;left:56px;top:840px;width:56px;height:48px;background:var(--white)}
  .quote-text{position:absolute;left:90px;top:903px;width:942px;font-size:19.5px;line-height:25px;letter-spacing:-.4px;text-align:justify;color:var(--ink)}

  .card{position:absolute;top:1078px;width:470px;height:456px;background:var(--white);border:2px dashed #6d6d6d;border-radius:26px;overflow:hidden}
  .card--nutrition{left:62px}
  .card--feeding{left:582px}
  .card-head{height:92px;background:var(--brown);color:var(--white);font-weight:700;font-size:23px;display:flex;align-items:center;justify-content:center;border-radius:24px 24px 0 0}
  .card-title{position:absolute;left:0;width:100%;top:115px;text-align:center;font-size:25px;letter-spacing:.3px;color:var(--ink)}

  .stat{position:absolute;width:190px;height:42px;font-size:20px;display:flex;align-items:center;padding-left:12px}
  .stat--plain{background:var(--grey);color:#333}
  .stat--key{background:var(--red-bright);color:var(--white);font-weight:700;justify-content:center;padding-left:0}
  .dotted-rule{position:absolute;left:37px;top:284px;width:390px;border-top:3px dotted #555}
  .ingredients{position:absolute;left:37px;top:305px;width:392px;font-size:14.5px;line-height:18px;letter-spacing:-.3px;text-align:justify;color:#333}

  .plan-title{position:absolute;left:48px;top:115px;font-size:25px;color:var(--ink)}
  .plan{position:absolute;left:38px;top:160px;width:376px;border-collapse:collapse;font-size:21.5px;color:var(--ink)}
  .plan th{font-weight:400;font-size:19px;text-align:left;height:34px}
  .plan td{height:34px}
  .plan th:first-child,.plan td:first-child{padding-left:12px;width:262px}
  .plan tbody tr:nth-child(even) td{background:var(--grey-row)}
</style>
</head>
<body>
<main class="insert">

  <svg class="hero-band" viewBox="0 0 1120 600" aria-hidden="true">
    <defs>
      <linearGradient id="heroRed" x1="0" y1="0" x2="1" y2="1">
        <stop offset="0" stop-color="#a9170f"/>
        <stop offset="1" stop-color="#93130c"/>
      </linearGradient>
      <pattern id="scallopDown" x="0" y="0" width="24" height="14" patternUnits="userSpaceOnUse">
        <circle cx="12" cy="2" r="12" fill="#9c150d"/>
      </pattern>
    </defs>
    <rect x="0" y="0" width="1120" height="570" fill="url(#heroRed)"/>
    <rect x="0" y="568" width="1120" height="14" fill="url(#scallopDown)"/>
  </svg>

  <svg class="foot-band" viewBox="0 0 1120 214" aria-hidden="true">
    <defs>
      <pattern id="scallopUp" x="0" y="0" width="24" height="14" patternUnits="userSpaceOnUse">
        <circle cx="12" cy="12" r="12" fill="#a9170f"/>
      </pattern>
    </defs>
    <rect x="0" y="0" width="1120" height="14" fill="url(#scallopUp)"/>
    <rect x="0" y="12" width="1120" height="202" fill="#a9170f"/>
  </svg>

  <header class="brand-tab">
    <span class="brand-dot"></span>
    <span class="brand-name">VERRA</span>
  </header>

  <svg class="dog-photo" viewBox="0 0 624 792" role="img" aria-label="Photo of a seated beagle puppy looking forward">
    <defs>
      <radialGradient id="dogTone" cx=".55" cy=".45" r=".6">
        <stop offset="0" stop-color="#e9dfd6"/>
        <stop offset=".55" stop-color="#b77a48"/>
        <stop offset="1" stop-color="#a9170f" stop-opacity="0"/>
      </radialGradient>
    </defs>
    <rect width="624" height="792" fill="url(#dogTone)"/>
  </svg>

  <h1 class="headline">Prepared<br>with love<br>for Shadow</h1>

  <h2 class="story-title">Our <span>Story</span></h2>
  <div class="story-dots"><i></i><i></i><i></i></div>
  <p class="story-lead">We Revolutionized the industry. Not Formulated<br>to meet a minimum standard, but to develop the<br>maximum health of the whole dog.</p>

  <div class="quote-box"></div>
  <svg class="quote-mark" viewBox="0 0 56 48" aria-hidden="true">
    <rect width="56" height="48" fill="#ffffff"/>
    <path d="M6 44 V24 C6 12 12 6 22 4 L24 10 C18 12 16 16 16 20 H24 V44 Z M32 44 V24 C32 12 38 6 48 4 L50 10 C44 12 42 16 42 20 H50 V44 Z" fill="#3e1008"/>
  </svg>
  <p class="quote-text">We didn't just set about to create a food that will ‘pass a minimum standard’. We set out to revolutionize the industry by creating a food that is designed with Superfoods, Wholesoe Grains, and Powertul Oils to help your dog achieve their maximu health,happiness andlongevity.’</p>

  <section class="card card--nutrition">
    <h3 class="card-head">We prepared the best for Shadow</h3>
    <p class="card-title">NUTRITIONAL INFORMATION</p>
    <div class="stat stat--plain" style="left:37px;top:164px">Protein: 15%</div>
    <div class="stat stat--key" style="left:235px;top:164px">Total Fat: 9.5%</div>
    <div class="stat stat--plain" style="left:37px;top:214px">Crude Fiber: 2.0%</div>
    <div class="stat stat--key" style="left:235px;top:214px">Moisture: 72%</div>
    <div class="dotted-rule"></div>
    <p class="ingredients">Potassium Citrate, DiCalcium Phosphate, Calcium Carbonate, Garbanzo Beans, Choline Bitartrate, Taurine, Salt, Zinc Proteinate, Magnesium Oxide, Iron Proteinate, Vitamin B-12, Selenium, Niacin, Riboflavin, Calcium Panthothen- ate, Thiamine, Vitamin A, Vitamin D, Calcium Iodate, Vitamin B6, Folic Acid</p>
  </section>

  <section class="card card--feeding">
    <h3 class="card-head">How much should I feed Shadow?</h3>
    <p class="plan-title">RECOMMENDED FEEDING PLAN</p>
    <table class="plan">
      <thead><tr><th>APPROXIMATE WEIGHT</th><th>FULL MEAL</th></tr></thead>
      <tbody>
        <tr><td>&lt;20 lbs</td><td>110 g</td></tr>
        <tr><td>20-29 lbs</td><td>200 g</td></tr>
        <tr><td>30-39 lbs</td><td>250 g</td></tr>
        <tr><td>40-54 lbs</td><td>300 g</td></tr>
        <tr><td>55-69 lbs</td><td>350 g</td></tr>
        <tr><td>70-85 lbs</td><td>400 g</td></tr>
        <tr><td>85+ lbs</td><td>500 g</td></tr>
      </tbody>
    </table>
  </section>

</main>
</body>
</html>
```